DELCOURT ROOFING YARD SIGN

We need a yard sign to put in our customers' yards when we are roofing their home.
Delcourt Roofing
417 Tobin Rd
Lake Charles LA 70615
phone: 337-555-0182

Maybe some verbiage like "Your Hometown Roofing Experts"
or
"Family Owned Since 1956"

```html
<!DOCTYPE html>
<html lang="en">
<head>
<meta charset="utf-8">
<title>Delcourt Roofing Yard Sign</title>
<link rel="stylesheet" href="https://fonts.googleapis.com/css2?family=Cinzel:wght@700;900&family=Philosopher:wght@700&display=swap">
<style>
  :root {
    --page: #e4e4e4;
    --wood-dark: #2f1a12;
    --wood-mid: #4b2e20;
    --wood-light: #5e3b29;
    --band-light: #eee6cf;
    --band-dark: #d3c6a8;
    --cream: #fdf7d9;
    --brown: #3a160c;
    --badge-white: #ffffff;
    --badge-ring: #b9b9b9;
  }
  html, body {
    margin: 0;
    width: 1200px;
    height: 1174px;
    overflow: hidden;
    background: var(--page);
  }
  .sign {
    position: absolute;
    left: 40px;
    top: 423px;
    width: 1120px;
    height: 328px;
    box-shadow: 0 14px 30px rgba(0,0,0,.35);
    overflow: hidden;
  }
  .sign__wood {
    position: absolute;
    inset: 0;
    width: 100%;
    height: 100%;
  }
  .sign__band {
    position: absolute;
    left: 337px;
    right: 0;
    top: 117px;
    height: 130px;
    background: linear-gradient(90deg, var(--band-dark) 0%, var(--band-light) 30%, var(--band-light) 75%, var(--band-dark) 100%);
    box-shadow: 0 2px 6px rgba(0,0,0,.35);
  }
  .sign__title {
    position: absolute;
    left: 360px;
    width: 720px;
    top: 28px;
    margin: 0;
    text-align: center;
    white-space: nowrap;
    font: 900 62px/1 "Cinzel", serif;
    color: var(--cream);
  }
  .sign__tagline {
    position: absolute;
    left: 390px;
    width: 646px;
    top: 127px;
    margin: 0;
    text-align: center;
    font: 900 50px/56px "Cinzel", serif;
    color: var(--brown);
    white-space: nowrap;
  }
  .sign__contact {
    position: absolute;
    left: 450px;
    width: 566px;
    top: 263px;
    margin: 0;
    text-align: center;
    font: 700 26px/28px "Philosopher", sans-serif;
    color: var(--cream);
    font-style: normal;
  }
  .badge {
    position: absolute;
    left: 34px;
    top: 16px;
    width: 304px;
    height: 304px;
    border-radius: 50%;
    background: var(--badge-white);
    border: 5px solid var(--badge-ring);
    box-sizing: border-box;
    box-shadow: 4px 6px 14px rgba(0,0,0,.55);
    display: flex;
    align-items: center;
    justify-content: center;
  }
  .badge__name {
    margin: 0;
    text-align: center;
    font: 700 34px/1.15 "Philosopher", sans-serif;
    color: var(--brown);
  }
</style>
</head>
<body>
  <section class="sign">
    <svg class="sign__wood" viewBox="0 0 1120 328" preserveAspectRatio="none" role="img" aria-label="Dark brown wood plank texture">
      <defs>
        <linearGradient id="woodTone" x1="0" y1="0" x2="1" y2="0">
          <stop offset="0" stop-color="#3a2217"/>
          <stop offset="0.5" stop-color="#4b2e20"/>
          <stop offset="1" stop-color="#3a2217"/>
        </linearGradient>
      </defs>
      <rect width="1120" height="328" fill="url(#woodTone)"/>
    </svg>

    <div class="sign__band"></div>

    <h1 class="sign__title">DELCOURT ROOFING</h1>
    <p class="sign__tagline">YOUR HOMETOWN<br>ROOFING EXPERTS</p>
    <address class="sign__contact">417 Tobin Rd, Lake Charles LA 70615<br>Phone: 337-555-0182</address>

    <div class="badge">
      <p class="badge__name">Delcourt<br>Roofing</p>
    </div>
  </section>
</body>
</html>
```